Web Developer Needs a Business Card Design

I need a personal business card design that represents me as a web developer for potential employers. I would like the background to be a dark color on the front for contrast with my logo and name. The back will have all my information along with a smaller version of the logo. I want something with a modern look and feel, not too conservative. This will be used for potential employers and freelance work.

Industry/Entity Type

Business

Contact Information for Business Card

Front should have my logo and name. The back should have all my personal information which would include: name: Tom Varulek, phone: 570-614-3098, email: tomvarulek@quillbox.net, website url: www.tomvarulek.net, logo, web developer.

Font styles to use
Sans Serif

Requirements
Must have
• Must include my logo. The color palette base color will be the logo color.

```html
<!DOCTYPE html>
<html lang="en">
<head>
<meta charset="utf-8">
<title>Tom Varulek — Business Card</title>
<link rel="stylesheet" href="https://fonts.googleapis.com/css2?family=Lato:wght@400;700&display=swap">
<style>
  :root {
    --page-bg: #141414;
    --card-bg: #0b0b0b;
    --card-edge: #262626;
    --accent: #74cdb9;
    --text-light: #f2f2f2;
    --text-muted: #d6d6d6;
  }
  * { box-sizing: border-box; margin: 0; padding: 0; }
  html, body {
    width: 1200px; height: 864px; overflow: hidden;
    background: var(--page-bg);
    font-family: "Lato", sans-serif;
  }
  .stage {
    width: 1200px; height: 864px;
    display: flex; align-items: center; justify-content: center; gap: 50px;
  }
  .card {
    position: relative;
    width: 525px; height: 300px;
    background: linear-gradient(160deg, #1a1a1a 0%, var(--card-bg) 55%, #050505 100%);
    border: 1px solid var(--card-edge);
    box-shadow: 0 18px 40px rgba(0,0,0,0.6);
  }
  .brand-mark {
    display: block;
    border-radius: 50%;
    border: 3px solid var(--accent);
    background: var(--accent);
    margin: 0 auto;
  }
  .card-front {
    display: flex; flex-direction: column; align-items: center; justify-content: center;
  }
  .card-front .brand-mark { width: 62px; height: 62px; }
  .card-front .brand-name {
    margin-top: 14px;
    color: var(--text-light);
    font-size: 24px; font-weight: 400; letter-spacing: 0.5px;
  }
  .card-back .brand-mark { width: 44px; height: 44px; margin-top: 32px; }
  .card-back .brand-name {
    margin-top: 8px; text-align: center;
    color: var(--text-light);
    font-size: 20px; font-weight: 400; letter-spacing: 0.5px;
  }
  .identity {
    position: relative; margin-top: 30px; height: 40px;
  }
  .identity-rule {
    position: absolute; left: 0; right: 0; top: 14px;
    height: 1px; background: var(--accent);
  }
  .identity-text {
    position: relative; width: 200px; margin: 0 auto;
    background: var(--card-bg); text-align: center;
  }
  .person-name {
    color: var(--accent); font-size: 18px; font-weight: 400; letter-spacing: 1px; line-height: 26px;
  }
  .person-role {
    color: var(--text-muted); font-size: 11px; font-weight: 700; letter-spacing: 1.5px;
    border-bottom: 1px solid var(--accent); display: inline-block; padding-bottom: 2px;
  }
  .contacts {
    display: flex; justify-content: space-between; align-items: flex-start;
    padding: 14px 22px 0;
  }
  .contact {
    display: flex; flex-direction: column; align-items: center; gap: 8px;
    color: var(--text-muted); font-size: 12px;
  }
  .contact-icon {
    width: 13px; height: 13px; background: var(--accent); border-radius: 2px;
    display: flex; align-items: center; justify-content: center;
  }
</style>
</head>
<body>
<main class="stage">
  <section class="card card-front" aria-label="Card front">
    <span class="brand-mark" aria-hidden="true"></span>
    <p class="brand-name">TOM VARULEK</p>
  </section>

  <section class="card card-back" aria-label="Card back">
    <span class="brand-mark" aria-hidden="true"></span>
    <p class="brand-name">TOM VARULEK</p>

    <div class="identity">
      <span class="identity-rule"></span>
      <div class="identity-text">
        <p class="person-name">TOM VARULEK</p>
        <p class="person-role">WEB DEVELOPER</p>
      </div>
    </div>

    <div class="contacts">
      <div class="contact">
        <span class="contact-icon">
          <svg width="9" height="9" viewBox="0 0 10 10" aria-hidden="true"><path d="M2 1 L4 1 L4.6 3.2 L3.4 4 Q4.3 5.8 6 6.6 L6.8 5.4 L9 6 L9 8 Q5 9 2.5 6.5 Q0.8 4.5 2 1Z" fill="#0b0b0b"/></svg>
        </span>
        <span>(570) 614-3098</span>
      </div>
      <div class="contact">
        <span class="contact-icon">
          <svg width="9" height="9" viewBox="0 0 10 10" aria-hidden="true"><rect x="1" y="2.5" width="8" height="5.5" fill="none" stroke="#0b0b0b" stroke-width="1"/><path d="M1 2.5 L5 5.8 L9 2.5" fill="none" stroke="#0b0b0b" stroke-width="1"/></svg>
        </span>
        <span>tomvarulek@quillbox.net</span>
      </div>
      <div class="contact">
        <span class="contact-icon">
          <svg width="9" height="9" viewBox="0 0 10 10" aria-hidden="true"><circle cx="5" cy="5" r="3.8" fill="none" stroke="#0b0b0b" stroke-width="1"/><ellipse cx="5" cy="5" rx="1.6" ry="3.8" fill="none" stroke="#0b0b0b" stroke-width="0.8"/><line x1="1.2" y1="5" x2="8.8" y2="5" stroke="#0b0b0b" stroke-width="0.8"/></svg>
        </span>
        <span>www.tomvarulek.net</span>
      </div>
    </div>
  </section>
</main>
</body>
</html>
```